Road Construction Company needs business cards

We would like a new business card designed for our business.

We're a road construction company based in Qld, Australia.

Can the business card please have the following information on it.

Name: Warren Halbeck
Position: General Manager
Phone: 0472 915 348
Email: Warren.halbeck@tovrin.com.au
Address: 87 Marrow Ave, Pendlebay, QLD, 4023
Website: www.tovrin.com.au

Visually we'd like the card to be professional and simple.

Attached is our logo.

Our website is www.tovrin.com.au

Target Market(s)

Men aged 25-60

Contact Information for Business Card

As listed in project description

Font styles to use
Serif

Requirements
Must have
• Large logo on back of card

```html
<!DOCTYPE html>
<html lang="en">
<head>
<meta charset="utf-8">
<title>Tovrin Road Construction – Business Card</title>
<link rel="stylesheet" href="https://fonts.googleapis.com/css2?family=Montserrat:wght@400;500;600;800&display=swap">
<style>
  :root {
    --bg: #c9c9c9;
    --brand-blue: #0d55a6;
    --brand-sky: #2fa3da;
    --paper: #ffffff;
    --mark-tone: #2a78c0;
  }
  * { box-sizing: border-box; margin: 0; padding: 0; }
  html, body { width: 1200px; height: 815px; overflow: hidden; }
  body {
    background: var(--bg);
    font-family: "Montserrat", Arial, sans-serif;
    display: flex;
    flex-direction: column;
    align-items: center;
    justify-content: center;
    gap: 40px;
  }
  .card {
    position: relative;
    width: 620px;
    height: 354px;
    border-radius: 28px;
    overflow: hidden;
    box-shadow: 0 8px 22px rgba(0,0,0,0.25);
  }
  .card-front { background: var(--paper); }
  .front-wave { position: absolute; inset: 0; display: block; }

  .wordmark {
    position: absolute;
    left: 140px;
    top: 50px;
    font-weight: 800;
    font-size: 56px;
    letter-spacing: 2px;
    color: var(--brand-blue);
    line-height: 1;
    white-space: nowrap;
  }

  .contact {
    position: absolute;
    left: 38px;
    top: 222px;
    color: var(--paper);
  }
  .contact-name {
    font-weight: 600;
    font-size: 25px;
    color: var(--brand-sky);
    line-height: 1.1;
  }
  .contact-role {
    font-weight: 500;
    font-size: 14px;
    margin-bottom: 10px;
  }
  .contact-line {
    display: flex;
    align-items: center;
    gap: 8px;
    font-size: 13.5px;
    line-height: 21px;
    white-space: nowrap;
  }
  .contact-icon { width: 14px; height: 14px; flex: none; }

  .address {
    position: absolute;
    right: 34px;
    top: 168px;
    text-align: right;
    color: var(--paper);
    font-size: 15px;
    line-height: 1.35;
    font-style: normal;
    white-space: nowrap;
  }

  .card-back {
    background: var(--brand-blue);
    display: flex;
    align-items: center;
    justify-content: center;
  }
  .wordmark-large {
    font-weight: 800;
    font-size: 118px;
    letter-spacing: 4px;
    color: var(--mark-tone);
    line-height: 1;
  }
</style>
</head>
<body>

<section class="card card-front" aria-label="Business card front">
  <svg class="front-wave" viewBox="0 0 620 354" aria-hidden="true">
    <path d="M0,214 C120,176 250,176 372,140 C482,106 530,58 496,0 L620,0 L620,354 L0,354 Z" fill="var(--brand-sky)"/>
    <path d="M0,226 C130,188 262,186 386,150 C498,116 548,64 518,0 L620,0 L620,354 L0,354 Z" fill="var(--brand-blue)"/>
    <path d="M0,226 C130,188 262,186 386,150 C498,116 548,64 518,0" fill="none" stroke="var(--paper)" stroke-width="4"/>
  </svg>

  <div class="wordmark">TOVRIN</div>

  <div class="contact">
    <div class="contact-name">Warren Halbeck</div>
    <div class="contact-role">General Manager</div>
    <div class="contact-line">
      <svg class="contact-icon" viewBox="0 0 16 16"><path d="M3.5 1.5l2.5 0 1 3.5-1.6 1.2a8 8 0 0 0 4.4 4.4L11 9l3.5 1v2.5c0 1-1 2-2 2A11 11 0 0 1 1.5 3.5c0-1 1-2 2-2z" fill="var(--brand-sky)"/></svg>
      <span>0472 915 348</span>
    </div>
    <div class="contact-line">
      <svg class="contact-icon" viewBox="0 0 16 16"><rect x="1" y="3" width="14" height="10" rx="1.5" fill="var(--brand-sky)"/><path d="M1.5 4l6.5 5 6.5-5" fill="none" stroke="var(--brand-blue)" stroke-width="1.4"/></svg>
      <span>Warren.halbeck@tovrin.com.au</span>
    </div>
    <div class="contact-line">
      <svg class="contact-icon" viewBox="0 0 16 16"><circle cx="8" cy="8" r="7" fill="var(--brand-sky)"/><path d="M1 8h14M8 1c-3 3.5-3 10.5 0 14M8 1c3 3.5 3 10.5 0 14" fill="none" stroke="var(--brand-blue)" stroke-width="1"/></svg>
      <span>www.tovrin.com.au</span>
    </div>
  </div>

  <address class="address">
    87 Marrow Ave,<br>
    Pendlebay, QLD, 4023
  </address>
</section>

<section class="card card-back" aria-label="Business card back">
  <div class="wordmark-large">TOVRIN</div>
</section>

</body>
</html>
```